Business card design needed

I run a Beautician studio (for 7 years now)
I offer
- Velmo Body Sugaring
- Ruby Glaze
- Nails
- Facials
- Manicure
- Foot Treatment
It might not be necessary to list all those treatments?
Maybe the link to the Website is sufficient?
I leave that up to you ...
(more info on www.FernAndDewByLenka.com.au)
Velmo BodySugaring is our biggest success, It replaces waxing.
I would like to incorporate the logo into the Business Card.
We had many complaints regarding our old Business Cards as the Phone Number was to small.
On the backside, we would like a "your next Appointment" section.
Looking forward to you Design, cheers ... Lenka
Industry/Entity Type
Business
Contact Information for Business Card
Fern by Dew by Lenka
14 Korrin Sqr 3942 Berwick
www.FernAndDewByLenka.com.au
03 9481 2267

```html
<!DOCTYPE html>
<html lang="en">
<head>
<meta charset="utf-8">
<title>Fern &amp; Dew by Lenka – Business Card</title>
<link href="https://fonts.googleapis.com/css2?family=Didact+Gothic&family=PT+Sans:ital,wght@0,400;1,700&family=Tinos&display=swap" rel="stylesheet">
<style>
  :root {
    --stage: #e7e3de;
    --card: #ffffff;
    --ink: #2f2f2f;
    --ink-soft: #555555;
    --band-dark: #58585a;
    --band-mid: #8e8e90;
    --band-light: #c9c9cb;
    --rule: #9a9a9a;
    --sun: #f0a12a;
    --brand: #3d3d3d;
    --faint: rgba(120, 110, 90, 0.13);
  }
  * { box-sizing: border-box; margin: 0; padding: 0; }
  html, body { width: 1200px; height: 788px; overflow: hidden; }
  body {
    position: relative;
    background: var(--stage);
    font-family: "PT Sans", sans-serif;
    color: var(--ink);
  }
  .side-label {
    position: absolute;
    font-family: "PT Sans", sans-serif;
    font-size: 21px;
    color: #222;
  }
  .card {
    position: absolute;
    width: 526px;
    height: 300px;
    background: var(--card);
    border-radius: 22px;
    overflow: hidden;
    box-shadow: 0 4px 10px rgba(0,0,0,0.25);
  }
  .card > * { position: absolute; }
  .card--front { left: 337px; top: 74px; }
  .card--back-offer { left: 53px; top: 443px; }
  .card--back-hours { left: 621px; top: 443px; }

  .studio-name {
    font-family: "Didact Gothic", sans-serif;
    letter-spacing: 1.5px;
    color: var(--ink);
    white-space: nowrap;
  }
  .brand-mark {
    display: flex;
    flex-direction: column;
    align-items: center;
    font-family: "PT Sans", sans-serif;
    font-size: 14px;
    line-height: 16px;
    letter-spacing: 2px;
    color: var(--brand);
    text-align: center;
    white-space: nowrap;
  }
  .brand-mark .dot {
    width: 40px; height: 40px;
    border-radius: 50%;
    background: var(--sun);
    margin-bottom: 5px;
  }

  /* front */
  .card--front .studio-name { left: 21px; top: 86px; font-size: 34px; }
  .card--front .brand-mark { left: 376px; top: 28px; width: 140px; }
  .contact { left: 27px; top: 176px; font-size: 17px; line-height: 23px; }
  .contact b { font-style: italic; font-weight: 700; }
  .swoosh { left: 0; top: 200px; width: 526px; height: 100px; }
  .website {
    right: 24px; bottom: 12px;
    color: #fff; font-size: 15px;
  }
  .website b { font-style: italic; }

  /* back one */
  .card--back-offer .studio-name { left: 0; width: 100%; top: 12px; text-align: center; font-size: 26px; }
  .title-rule { left: 0; top: 51px; width: 100%; height: 1px; background: var(--ink-soft); }
  .heading { font-style: italic; font-weight: 700; font-size: 18px; }
  .offer-heading { left: 30px; top: 70px; }
  .offer-list {
    left: 30px; top: 97px;
    list-style: none;
    font-family: "Tinos", serif;
    font-size: 15px; line-height: 20px; color: var(--ink-soft);
  }
  .offer-list li::before {
    content: ""; display: inline-block;
    width: 5px; height: 5px; background: var(--ink-soft);
    margin-right: 8px; vertical-align: middle;
  }
  .column-rule { left: 206px; top: 72px; width: 3px; height: 148px; background: linear-gradient(#d0d0d0, #777, #d0d0d0); }
  .appointment-heading { left: 244px; top: 70px; }
  .field { left: 244px; font-size: 17px; display: flex; align-items: flex-end; width: 265px; }
  .field .blank { flex: 1; border-bottom: 1px solid var(--ink); height: 16px; margin-left: 2px; }
  .field .suffix { margin-left: 4px; }
  .faint-brand {
    left: 130px; top: 190px;
    font-family: "PT Sans", sans-serif;
    font-size: 56px; letter-spacing: 10px;
    color: var(--faint);
  }
  .hours-heading { left: 0; width: 100%; top: 238px; text-align: center; font-size: 15px; font-style: italic; font-weight: 700; }
  .hours-line { left: 0; width: 100%; top: 261px; text-align: center; font-size: 13px; word-spacing: 2px; }
  .hours-line span + span { margin-left: 44px; }

  /* back two */
  .card--back-hours .heading { left: 33px; top: 28px; font-size: 21px; letter-spacing: 1.2px; }
  .hours-list { left: 30px; top: 61px; font-size: 18px; line-height: 24px; }
  .card--back-hours .brand-mark { left: 372px; top: 18px; width: 130px; }
  .section-rule { left: 31px; top: 117px; width: 464px; height: 1px; background: var(--rule); }
  .next-appointment { left: 46px; top: 144px; font-size: 19px; display: flex; align-items: flex-end; }
  .next-appointment .blank { width: 260px; border-bottom: 1px solid var(--ink); margin-right: 4px; height: 18px; }
  .date-row { left: 35px; top: 194px; font-size: 19px; display: flex; align-items: flex-end; gap: 5px; }
  .date-row .blank { border-bottom: 1px solid var(--ink); height: 18px; }
  .day-row { left: 59px; top: 248px; display: flex; gap: 20px; font-size: 17px; }
  .day-row label { display: flex; align-items: center; gap: 10px; }
  .day-row .box { width: 23px; height: 23px; border: 1px solid var(--ink); }
</style>
</head>
<body>

<div class="side-label" style="left:572px; top:34px;">Front</div>
<div class="side-label" style="left:284px; top:404px;">Back - 1</div>
<div class="side-label" style="left:857px; top:404px;">Back - 2</div>

<section class="card card--front">
  <h1 class="studio-name">FERN&amp;DEW BY LENKA</h1>
  <div class="brand-mark">
    <span class="dot"></span>
    <span>VELMO</span>
    <span>BODY SUGARING</span>
  </div>
  <p class="contact"><b>phone</b> 03 9481 2267<br><b>add</b> 14 Korrin Sqr, 3942 Berwick</p>
  <svg class="swoosh" viewBox="0 0 526 100" preserveAspectRatio="none" aria-hidden="true">
    <path d="M0 28 C120 52 260 40 526 0 L526 100 L0 100 Z" fill="var(--band-light)"/>
    <path d="M0 44 C140 62 300 46 526 6 L526 100 L0 100 Z" fill="#ffffff"/>
    <path d="M0 52 C150 70 300 50 526 10 L526 100 L0 100 Z" fill="var(--band-mid)"/>
    <path d="M0 66 C170 78 320 56 526 14 L526 100 L0 100 Z" fill="#ffffff"/>
    <path d="M0 74 C180 84 330 62 526 18 L526 100 L0 100 Z" fill="var(--band-dark)"/>
  </svg>
  <p class="website"><b>w</b> www.FernAndDewByLenka.com.au</p>
</section>

<section class="card card--back-offer">
  <div class="faint-brand" aria-hidden="true">VELMO</div>
  <h2 class="studio-name">FERN&amp;DEW BY LENKA</h2>
  <div class="title-rule"></div>
  <h3 class="heading offer-heading">I offer</h3>
  <ul class="offer-list">
    <li>Velmo Body Sugaring</li>
    <li>Ruby Glaze</li>
    <li>Nails</li>
    <li>Facials</li>
    <li>Manicure</li>
    <li>Foot Treatment</li>
  </ul>
  <div class="column-rule"></div>
  <h3 class="heading appointment-heading">An Appointment</h3>
  <div class="field" style="top:112px;">Name<span class="blank"></span></div>
  <div class="field" style="top:152px;">Date<span class="blank"></span></div>
  <div class="field" style="top:192px; width:267px;">time<span class="blank"></span><span class="suffix">am / pm</span></div>
  <h4 class="hours-heading">Hours of Operation</h4>
  <p class="hours-line"><span>Mon. to Fri.&nbsp; 7.30am - 7.00pm</span><span>Sat. 7.30am - 12.00pm</span></p>
</section>

<section class="card card--back-hours">
  <h3 class="heading">Hours of Operation</h3>
  <p class="hours-list">Monday to Friday -&nbsp; 7.30am - 7.00pm<br>Saturday - 7.30am - 12.00pm</p>
  <div class="brand-mark">
    <span class="dot"></span>
    <span>VELMO</span>
    <span>BODY SUGARING</span>
  </div>
  <div class="section-rule"></div>
  <p class="next-appointment"><span class="blank"></span>has an appointment</p>
  <p class="date-row">Date :<span class="blank" style="width:40px"></span>/<span class="blank" style="width:40px"></span>/<span class="blank" style="width:52px"></span>&nbsp;@<span class="blank" style="width:40px"></span>:<span class="blank" style="width:52px"></span>am / pm</p>
  <div class="day-row">
    <label><span class="box"></span>Mon.</label>
    <label><span class="box"></span>Tue.</label>
    <label><span class="box"></span>Wed.</label>
    <label><span class="box"></span>Thu.</label>
    <label><span class="box"></span>Fri.</label>
  </div>
</section>

</body>
</html>
```